Hartwell Estates Business Cards

I would like a business card that includes myself and my partner.
Includes: Logo, office #, email, website, our names, our numbers and possibly the address. I would also like the logo to be embossed and the card to be horizontal.
There is a photo of our yard signs to give you an idea of the colors of our business.

Target Market(s)

Everyone in real estate market.
We are in a rural area. Our clientele are from all socioeconomic backgrounds.

Industry/Entity Type

Real Estate Agent

Contact Information for Business Card

Company Name: Hartwell Estates
Our Names, Titles & Cell #'s : Dana Pembrook-Broker (555).317.6624, Marla Pembrook-Realtor (555).609.1385
Office #: (555).240.3918
Website: hartwellestates-demo.com
Joint Email: pembrook@hartwellestates-demo.com
Office Address: 418B W. Calloway Ave.
Millbrook, OK. 70913

Font styles to use
Serif

Requirements
Must have
• HORIZONTAL, Logo, Myself and my partners names, Our cell #'s, our office #, our website, our email address
Nice to have
• Embossed logo, office address, our titles.

```html
<!DOCTYPE html>
<html lang="en">
<head>
<meta charset="utf-8">
<title>Hartwell Estates Business Cards</title>
<link href="https://fonts.googleapis.com/css2?family=Source+Sans+3:wght@400;600&display=swap" rel="stylesheet">
<style>
  :root {
    --purple: #4a2366;
    --ink: #3d3742;
    --paper: #ffffff;
    --backdrop: #ece9ee;
    --rule: #8a8290;
  }
  * { box-sizing: border-box; margin: 0; padding: 0; }
  html, body { width: 1200px; height: 900px; overflow: hidden; }
  body {
    background: var(--backdrop);
    font-family: "Source Sans 3", "Helvetica Neue", Arial, sans-serif;
    position: relative;
  }
  .card {
    position: absolute;
    box-shadow: 0 6px 18px rgba(40, 20, 60, 0.18);
  }
  .card--front {
    left: 78px; top: 35px; width: 588px; height: 363px;
    background: var(--paper);
  }
  .card--back {
    left: 388px; top: 505px; width: 567px; height: 352px;
    background: var(--purple);
    color: var(--paper);
  }
  .wordmark {
    position: absolute;
    display: flex; align-items: center; gap: 16px;
    font-weight: 600;
    white-space: nowrap;
  }
  .wordmark__mark {
    width: 22px; height: 22px; border-radius: 50%;
    background: currentColor;
  }
  .card--front .wordmark {
    left: 0; right: 0; top: 50px; justify-content: center;
    color: var(--purple); font-size: 50px;
  }
  .card--back .wordmark {
    left: 0; right: 0; top: 140px; justify-content: center;
    font-size: 48px;
  }
  .agents {
    position: absolute; top: 163px; left: 0; right: 0;
    display: flex; justify-content: center;
  }
  .agent { width: 170px; line-height: 1.2; }
  .agent--left { text-align: right; padding-right: 12px; border-right: 1.5px solid var(--rule); }
  .agent--right { text-align: left; padding-left: 16px; }
  .agent__name { color: var(--purple); font-weight: 600; font-size: 19px; white-space: nowrap; }
  .agent__title, .agent__phone { color: var(--ink); font-size: 15px; }
  .agent__title { margin-top: 2px; }
  .contact {
    position: absolute; top: 248px; left: 0; right: 0;
    text-align: center; font-size: 15px; color: var(--ink); white-space: nowrap;
  }
  .contact b { color: var(--purple); font-weight: 600; }
  .contact__sep { margin: 0 6px 0 4px; }
  .address-band {
    position: absolute; left: 0; right: 0; bottom: 0; height: 70px;
    background: var(--purple); color: var(--paper);
    display: flex; align-items: center; justify-content: center;
    font-size: 15px;
  }
  .website {
    position: absolute; left: 0; right: 0; top: 258px;
    text-align: center; font-size: 15px;
  }
</style>
</head>
<body>
  <section class="card card--front" aria-label="Business card front">
    <div class="wordmark"><span class="wordmark__mark"></span><span>Hartwell Estates</span></div>
    <div class="agents">
      <div class="agent agent--left">
        <div class="agent__name">DANA PEMBROOK</div>
        <div class="agent__title">Broker</div>
        <div class="agent__phone">(555).317.6624</div>
      </div>
      <div class="agent agent--right">
        <div class="agent__name">MARLA PEMBROOK</div>
        <div class="agent__title">Realtor</div>
        <div class="agent__phone">(555).609.1385</div>
      </div>
    </div>
    <p class="contact"><b>P:</b> (555).240.3918<span class="contact__sep">|</span><b>E:</b> pembrook@hartwellestates-demo.com</p>
    <div class="address-band">418B W. Calloway Ave. Millbrook, OK. 70913</div>
  </section>

  <section class="card card--back" aria-label="Business card back">
    <div class="wordmark"><span class="wordmark__mark"></span><span>Hartwell Estates</span></div>
    <p class="website">www.hartwellestates-demo.com</p>
  </section>
</body>
</html>
```